BMR Going Cashless

Hello,
We are a medical office looking to get a flyer created to promote to our patients we will be going "Cashless." Our tagline will be "Cash-Less is Stress-Less"

"Starting in July, to offer you the fastest and most convenient service, we are transitioning to a cashless system. You can now enjoy faster checkout times and greater security with card and contactless payments. More info to come."

I've added two other flyers as sample designs we've used.

Please include logo, addresses, website, phone number

Files to include jpeg, png, pdf (under 5mb), Facebook and Instagram sizing.

Thank you,
Lowen

```html
<!DOCTYPE html>
<html lang="en">
<head>
<meta charset="utf-8">
<title>BMR Going Cashless</title>
<link href="https://fonts.googleapis.com/css2?family=Allison&family=Montserrat:wght@800;900&family=Oswald:wght@600&family=Poppins:wght@300;400;500;600;700&display=swap" rel="stylesheet">
<style>
:root{
  --board:#c2c2c2;
  --orange:#f47a45;
  --teal:#4fbf9f;
  --dark:#2b2b2c;
  --white:#ffffff;
  --paper:#f3f2f0;
  --label:#1f1f1f;
}
*{margin:0;padding:0;box-sizing:border-box}
html,body{width:1200px;height:2323px;overflow:hidden}
body{background:var(--board);font-family:"Poppins",sans-serif;position:relative;color:var(--white)}
.flyer{position:absolute;left:276px;width:648px;overflow:hidden;background:linear-gradient(180deg,#fbfbfa 0%,var(--paper) 60%,#e9e8e6 100%)}
.flyer--square{top:202px;height:646px}
.flyer--story{top:1016px;height:1151px}
.size-label{position:absolute;left:0;width:1200px;text-align:center;font-weight:300;font-size:54px;color:var(--label);letter-spacing:1px}
.abs{position:absolute}
.dark-field{position:absolute;left:0;top:0;width:648px}
.art{position:absolute;border-radius:14px;background:radial-gradient(ellipse at 65% 40%,#4a6fb0 0%,#3a4f7c 35%,#2f3446 70%,rgba(47,52,70,0) 100%)}
.headline{position:absolute;color:var(--orange);white-space:nowrap;line-height:1}
.headline .accent{color:var(--teal)}
.script{position:absolute;font-family:"Allison",cursive;color:var(--teal);line-height:1;white-space:nowrap}
.kicker{position:absolute;color:var(--teal);font-weight:500;letter-spacing:3px;line-height:1}
.month{position:absolute;background:var(--teal);color:var(--white);font-weight:700;line-height:1;clip-path:polygon(0 0,88% 0,100% 100%,0 100%);padding-left:5px}
.intro{position:absolute;line-height:1.2}
.rule{position:absolute;height:1px;background:var(--orange)}
.transition{position:absolute;white-space:nowrap}
.transition strong{color:var(--orange);font-weight:700}
.benefits{position:absolute;border:1px solid var(--orange);border-radius:10px}
.enjoy{position:absolute;line-height:1.05}
.enjoy span{color:var(--orange);display:block;font-weight:400}
.enjoy b{font-weight:700}
.benefit{position:absolute;line-height:1.2;padding-left:19px}
.benefit svg{position:absolute;left:0;top:3px}
.more{position:absolute;font-weight:700;letter-spacing:4px;white-space:nowrap}
.office{position:absolute;line-height:1.25;padding-left:14px}
.office svg{position:absolute;left:0;top:2px}
.office b{display:block;font-weight:700}
.brand{position:absolute;display:flex;align-items:center;gap:8px;color:var(--orange);font-weight:700;line-height:1.05}
.brand i{display:block;border-radius:50%;background:var(--teal);flex:none}
.phone{position:absolute;display:flex;align-items:center;gap:6px;font-weight:700;white-space:nowrap}
.web{position:absolute;background:var(--teal);color:var(--dark);clip-path:polygon(14px 0,100% 0,100% 100%,0 100%);display:flex;align-items:center;justify-content:center;font-weight:500;letter-spacing:6px}
.web b{font-weight:700}
</style>
</head>
<body>

<!-- Square feed version -->
<section class="flyer flyer--square">
  <svg class="dark-field" height="646" viewBox="0 0 648 646" aria-hidden="true">
    <path d="M0 305 L40 292 L30 300 L120 276 L95 288 L260 250 L230 262 L420 222 L400 232 L648 186 L648 646 L0 646 Z" fill="#2b2b2c"/>
  </svg>
  <div class="art" style="left:318px;top:78px;width:330px;height:343px" role="img" aria-label="Card payment terminal, smartphone budget app and bank card"></div>

  <h1 class="headline" style="left:32px;top:70px;font-family:'Oswald',sans-serif;font-weight:600;font-size:76px;letter-spacing:-1px">CASH-LESS IS</h1>
  <div class="script" style="left:28px;top:118px;font-size:112px">Stress-less</div>

  <div class="kicker" style="left:37px;top:327px;font-size:11px;color:var(--orange)">STARTING IN</div>
  <div class="month" style="left:37px;top:341px;width:104px;height:35px;font-size:34px;padding-top:2px">JULY</div>
  <p class="intro" style="left:150px;top:327px;font-size:12.5px">To offer you the<br>fastest &amp; most<br>convenient service,</p>
  <div class="rule" style="left:37px;top:376px;width:228px"></div>

  <p class="transition" style="left:31px;top:397px;font-size:14.5px">WE ARE TRANSITIONING TO A <strong>CASHLESS SYSTEM.</strong></p>

  <div class="benefits" style="left:78px;top:427px;width:537px;height:52px"></div>
  <p class="enjoy" style="left:33px;top:436px;font-size:16px"><span>YOU CAN</span><b>NOW ENJOY</b></p>
  <p class="benefit" style="left:152px;top:434px;font-size:15px"><svg width="12" height="12" viewBox="0 0 12 12"><circle cx="6" cy="6" r="6" fill="#f47a45"/><path d="M3.2 6.2 5.2 8 8.8 4" stroke="#fff" stroke-width="1.5" fill="none"/></svg>Faster checkout<br>times</p>
  <p class="benefit" style="left:314px;top:434px;font-size:15px"><svg width="12" height="12" viewBox="0 0 12 12"><circle cx="6" cy="6" r="6" fill="#f47a45"/><path d="M3.2 6.2 5.2 8 8.8 4" stroke="#fff" stroke-width="1.5" fill="none"/></svg>Greater security<br>with card</p>
  <p class="benefit" style="left:484px;top:434px;font-size:15px"><svg width="12" height="12" viewBox="0 0 12 12"><circle cx="6" cy="6" r="6" fill="#f47a45"/><path d="M3.2 6.2 5.2 8 8.8 4" stroke="#fff" stroke-width="1.5" fill="none"/></svg>Contactless<br>payments</p>

  <p class="more" style="left:232px;top:491px;font-size:17px;color:var(--orange)">MORE INFO TO COME..</p>

  <div class="brand" style="left:31px;top:524px;font-size:18px"><i style="width:34px;height:34px"></i>BMR FOOT<br>&amp; ANKLE</div>

  <p class="office" style="left:233px;top:521px;font-size:10.5px"><svg width="10" height="10" viewBox="0 0 10 10"><circle cx="5" cy="5" r="5" fill="#4fbf9f"/><circle cx="5" cy="4.5" r="1.6" fill="#2b2b2c"/></svg><b>Northgate Office</b>52 Linden Park<br>Dr. Suite 110<br>Ashford, MD21990</p>
  <p class="office" style="left:363px;top:521px;font-size:10.5px"><svg width="10" height="10" viewBox="0 0 10 10"><circle cx="5" cy="5" r="5" fill="#4fbf9f"/><circle cx="5" cy="4.5" r="1.6" fill="#2b2b2c"/></svg><b>Riverside Office</b>88 Willow Bend Lane<br>Carlow,<br>WV25990</p>
  <p class="office" style="left:508px;top:520px;font-size:10.5px"><svg width="10" height="10" viewBox="0 0 10 10"><circle cx="5" cy="5" r="5" fill="#4fbf9f"/><circle cx="5" cy="4.5" r="1.6" fill="#2b2b2c"/></svg><b>Eastfield Office</b>2710 Halden Court<br>Blvd. Suite 204<br>Eastfield, MD21995</p>

  <div class="phone" style="left:31px;top:585px;font-size:24px"><svg width="19" height="19" viewBox="0 0 20 20"><circle cx="10" cy="10" r="9" fill="none" stroke="#f47a45" stroke-width="2"/><path d="M6.5 5.5c.8-.8 1.6-.5 2 .3l.6 1.3c.3.6 0 1.1-.5 1.5.6 1.3 1.6 2.3 2.8 2.9.4-.5.9-.8 1.5-.5l1.3.6c.8.4 1.1 1.2.3 2-1.6 1.6-4 .5-5.9-1.4-1.9-1.9-3.1-4.2-1.5-5.8z" fill="#f47a45"/></svg>(555)014-2290</div>
  <div class="web" style="left:271px;top:589px;width:377px;height:24px;font-size:17px">www.<b>bmrfootcare</b>.com</div>
</section>
<p class="size-label" style="top:870px">1080 X 1080</p>

<!-- Story version -->
<section class="flyer flyer--story">
  <svg class="dark-field" height="1151" viewBox="0 0 648 1151" aria-hidden="true">
    <path d="M0 562 L50 545 L35 556 L150 526 L120 540 L300 500 L270 514 L470 476 L445 488 L648 455 L648 1151 L0 1151 Z" fill="#2b2b2c"/>
  </svg>

  <div class="brand" style="left:200px;top:62px;font-size:26px"><i style="width:52px;height:52px"></i>BMR FOOT<br>&amp; ANKLE</div>

  <h1 class="headline" style="left:0;width:648px;text-align:center;top:143px;font-family:'Montserrat',sans-serif;font-weight:900;font-size:71px;letter-spacing:-0.5px">CASH-LESS <span class="accent">IS</span></h1>
  <div class="script" style="left:0;width:648px;text-align:center;top:190px;font-size:128px">Stress-less</div>

  <div class="art" style="left:85px;top:300px;width:518px;height:420px" role="img" aria-label="Card payment terminal, smartphone budget app and bank card"></div>

  <div class="kicker" style="left:100px;top:740px;font-size:21px;letter-spacing:5px;color:var(--orange)">STARTING IN</div>
  <div class="month" style="left:100px;top:768px;width:183px;height:62px;font-size:60px;padding-left:7px">JULY</div>
  <p class="intro" style="left:309px;top:740px;font-size:22.5px">To offer you the<br>fastest &amp; most<br>convenient service,</p>
  <div class="rule" style="left:100px;top:830px;width:420px"></div>

  <p class="transition" style="left:65px;top:860px;font-size:20px">WE ARE TRANSITIONING TO A <strong>CASHLESS SYSTEM.</strong></p>

  <div class="benefits" style="left:101px;top:891px;width:496px;height:51px"></div>
  <p class="enjoy" style="left:57px;top:898px;font-size:16px"><span>YOU CAN</span><b>NOW ENJOY</b></p>
  <p class="benefit" style="left:172px;top:898px;font-size:14.5px"><svg width="11" height="11" viewBox="0 0 12 12"><circle cx="6" cy="6" r="6" fill="#f47a45"/><path d="M3.2 6.2 5.2 8 8.8 4" stroke="#fff" stroke-width="1.5" fill="none"/></svg>Faster checkout<br>times</p>
  <p class="benefit" style="left:325px;top:898px;font-size:14.5px"><svg width="11" height="11" viewBox="0 0 12 12"><circle cx="6" cy="6" r="6" fill="#f47a45"/><path d="M3.2 6.2 5.2 8 8.8 4" stroke="#fff" stroke-width="1.5" fill="none"/></svg>Greater security<br>with card</p>
  <p class="benefit" style="left:487px;top:898px;font-size:14.5px"><svg width="11" height="11" viewBox="0 0 12 12"><circle cx="6" cy="6" r="6" fill="#f47a45"/><path d="M3.2 6.2 5.2 8 8.8 4" stroke="#fff" stroke-width="1.5" fill="none"/></svg>Contactless<br>payments</p>

  <p class="more" style="left:0;width:648px;text-align:center;top:966px;font-size:20px;color:var(--teal)">MORE INFO TO COME..</p>

  <p class="office" style="left:58px;top:992px;font-size:11.5px"><svg width="11" height="11" viewBox="0 0 10 10"><circle cx="5" cy="5" r="5" fill="#4fbf9f"/><circle cx="5" cy="4.5" r="1.6" fill="#2b2b2c"/></svg><b style="margin-bottom:6px">Northgate Office</b>52 Linden Park<br>Dr. Suite 110<br>Ashford, MD21990</p>
  <p class="office" style="left:271px;top:992px;font-size:11.5px"><svg width="11" height="11" viewBox="0 0 10 10"><circle cx="5" cy="5" r="5" fill="#4fbf9f"/><circle cx="5" cy="4.5" r="1.6" fill="#2b2b2c"/></svg><b style="margin-bottom:6px">Riverside Office</b>88 Willow Bend Lane<br>Carlow,<br>WV25990</p>
  <p class="office" style="left:472px;top:992px;font-size:11.5px"><svg width="11" height="11" viewBox="0 0 10 10"><circle cx="5" cy="5" r="5" fill="#4fbf9f"/><circle cx="5" cy="4.5" r="1.6" fill="#2b2b2c"/></svg><b style="margin-bottom:6px">Eastfield Office</b>2710 Halden Court<br>Blvd. Suite 204<br>Eastfield, MD21995</p>

  <div class="phone" style="left:58px;top:1068px;font-size:25px"><svg width="20" height="20" viewBox="0 0 20 20"><circle cx="10" cy="10" r="9" fill="none" stroke="#f47a45" stroke-width="2"/><path d="M6.5 5.5c.8-.8 1.6-.5 2 .3l.6 1.3c.3.6 0 1.1-.5 1.5.6 1.3 1.6 2.3 2.8 2.9.4-.5.9-.8 1.5-.5l1.3.6c.8.4 1.1 1.2.3 2-1.6 1.6-4 .5-5.9-1.4-1.9-1.9-3.1-4.2-1.5-5.8z" fill="#f47a45"/></svg>(555)014-2290</div>
  <div class="web" style="left:276px;top:1072px;width:372px;height:25px;font-size:17px">www.<b>bmrfootcare</b>.com</div>
</section>
<p class="size-label" style="top:2188px">1920 X 1080</p>

</body>
</html>
```